Business Card Design for Property Development Company Director

I am looking for a professional and unforgettable business card design for our Director of our Property Development Company.
Please see attached .pptx file to find out what information to include. You don't have to follow the exact format shown in the file - I am interested to see your creative flair using the information provided.

```html
<!DOCTYPE html>
<html lang="en">
<head>
<meta charset="utf-8">
<title>Harwell Property Group – Business Card</title>
<link rel="stylesheet" href="https://fonts.googleapis.com/css2?family=Roboto:wght@400;500;700&family=Roboto+Condensed:wght@700&display=swap">
<style>
  :root {
    --brand-blue: #284a8e;
    --brand-blue-deep: #223f7a;
    --paper: #f2f2f2;
    --card-white: #f7f7f7;
    --edge-grey: #5b5d62;
    --text-white: #ffffff;
    --text-soft: #e3e8f3;
  }
  * { margin: 0; padding: 0; box-sizing: border-box; }
  html, body { width: 1200px; height: 726px; overflow: hidden; }
  body {
    background: var(--paper);
    font-family: "Roboto", Arial, sans-serif;
    position: relative;
  }
  .card {
    position: absolute;
    top: 209px;
    width: 540px;
    height: 308px;
    border-radius: 3px;
    overflow: hidden;
    box-shadow: 0 6px 18px rgba(0,0,0,0.15);
  }
  /* Front */
  .card-front {
    left: 40px;
    background: var(--brand-blue);
    color: var(--text-white);
    text-align: center;
  }
  .front-tagline {
    position: absolute;
    top: 34px;
    left: 0; right: 0;
    font-size: 17px;
    line-height: 21px;
    font-weight: 400;
  }
  .front-brand {
    position: absolute;
    top: 110px;
    left: 0; right: 0;
    display: flex;
    align-items: center;
    justify-content: center;
    gap: 16px;
  }
  .brand-square {
    width: 58px;
    height: 58px;
    background: var(--text-white);
  }
  .brand-name {
    text-align: left;
    font-weight: 700;
    color: var(--text-white);
    text-transform: uppercase;
  }
  .brand-name .brand-main { display: block; font-size: 46px; line-height: 44px; letter-spacing: 1px; }
  .brand-name .brand-sub { display: block; font-size: 15px; line-height: 20px; letter-spacing: 5px; }
  .front-invite {
    position: absolute;
    bottom: 38px;
    left: 0; right: 0;
    font-size: 14px;
  }
  /* Back */
  .card-back {
    left: 620px;
    background: var(--card-white);
  }
  .back-shape { position: absolute; inset: 0; }
  .back-brand {
    position: absolute;
    left: 448px;
    top: 154px;
    transform: translate(-50%, -50%) rotate(-90deg);
    white-space: nowrap;
    font-weight: 700;
    color: var(--brand-blue);
    text-transform: uppercase;
    display: flex;
    align-items: center;
    gap: 10px;
  }
  .back-brand .brand-square { width: 34px; height: 34px; background: var(--brand-blue); }
  .back-brand .brand-name { color: var(--brand-blue); }
  .back-brand .brand-main { font-size: 30px; line-height: 30px; }
  .back-brand .brand-sub { font-size: 10px; line-height: 14px; letter-spacing: 3.5px; }
  .person {
    position: absolute;
    left: 40px;
    top: 40px;
    color: var(--text-white);
  }
  .person-name {
    font-family: "Roboto Condensed", Arial, sans-serif;
    font-weight: 700;
    font-size: 19px;
  }
  .person-role { font-size: 12px; color: var(--text-soft); margin-top: 4px; margin-left: 12px; }
  .contacts {
    position: absolute;
    left: 40px;
    bottom: 34px;
    list-style: none;
    color: var(--text-white);
    font-size: 14px;
    line-height: 19px;
  }
  .contacts li { display: flex; align-items: center; gap: 12px; }
  .contacts svg { width: 13px; height: 13px; flex: none; }
  .contacts .licence { display: block; }
</style>
</head>
<body>

<section class="card card-front">
  <p class="front-tagline">Property Development<br>&amp; Site Acquisition Specialists</p>
  <div class="front-brand">
    <span class="brand-square"></span>
    <p class="brand-name"><span class="brand-main">Harwell</span><span class="brand-sub">Property Group</span></p>
  </div>
  <p class="front-invite">Ask me about our INVESTMENT &amp; PARTNERSHIP opportunities</p>
</section>

<section class="card card-back">
  <svg class="back-shape" viewBox="0 0 540 308" preserveAspectRatio="none">
    <path d="M0 0 H345 Q 300 150 405 308 H0 Z" fill="var(--edge-grey)" transform="translate(14 0)"/>
    <path d="M0 0 H345 Q 300 150 405 308 H0 Z" fill="var(--brand-blue)"/>
  </svg>
  <div class="back-brand">
    <span class="brand-square"></span>
    <p class="brand-name"><span class="brand-main">Harwell</span><span class="brand-sub">Property Group</span></p>
  </div>
  <div class="person">
    <h1 class="person-name">Daniel Forbes</h1>
    <p class="person-role">Director</p>
  </div>
  <ul class="contacts">
    <li><svg viewBox="0 0 16 16"><path d="M4 1l3 3-2 2c1 2 3 4 5 5l2-2 3 3-2 3C7 15 1 9 1 3z" fill="#fff"/></svg>0400 318 726</li>
    <li><svg viewBox="0 0 16 16"><rect x="1" y="3" width="14" height="10" fill="none" stroke="#fff" stroke-width="1.6"/><path d="M1 3l7 6 7-6" fill="none" stroke="#fff" stroke-width="1.6"/></svg>daniel@harwell.com.au</li>
    <li><svg viewBox="0 0 16 16"><circle cx="8" cy="8" r="6.5" fill="none" stroke="#fff" stroke-width="1.4"/><path d="M1.5 8h13M8 1.5c-3 3-3 10 0 13M8 1.5c3 3 3 10 0 13" fill="none" stroke="#fff" stroke-width="1.2"/></svg>www.harwell.com.au</li>
    <li class="licence">Real Estate Lic:<br>5102836 &amp; 5102837</li>
  </ul>
</section>

</body>
</html>
```